Mobile Friendly Lead Generation Landing Page

We are a web marketing company that specialized in web lead generation. Recently we have started buying media from mobile devices and we need a mobile interface(landing page) where we can collect user data in an effective manner.

Our current mobile landing page is:
http://www.tutorpath.example.com/lp13d/index.aspx?a=true&source=841356
Through this you can see what the steps/questions users need to answer to get matched to a school. We need the design for the whole process.

We are pretty open for design ideas and our goal is to make this mobile optimized landing page have the look and feel of an app...but not an app.
There are several questions in the process but we are open to changing the way they are presented. As in, you can have one question at a time or a few.
The goal is to make this EXTREMELY EASY for users to interact with.

One example that we have liked is:
http://learnvane.example/schools/57214-page1.lvne (please note that this opens only on mobile devices)

Some of these screenshots are attached.

Our web form looks like this:
http://www.tutorpath.example.com/lp88/index.aspx?a=true

```html
<!DOCTYPE html>
<html lang="en">
<head>
<meta charset="utf-8">
<title>TutorPath – Mobile Match Flow</title>
<link href="https://fonts.googleapis.com/css2?family=Roboto:wght@400;500;700&display=swap" rel="stylesheet">
<style>
  :root{
    --stage:#14597f;
    --stage-edge:#0d3f5e;
    --green:#6cc117;
    --green-dark:#4f9a0c;
    --sky:#13ade0;
    --sky-dark:#0b86b9;
    --orange:#ff5a0a;
    --ink:#2f3338;
    --paper:#f2f3f5;
    --cloud-top:#d6eaf8;
    --cloud-bottom:#e6f2fb;
    --white:#ffffff;
  }
  *{box-sizing:border-box;margin:0;padding:0}
  html,body{width:1200px;height:1000px;overflow:hidden}
  body{
    font-family:"Roboto",Arial,sans-serif;
    background:radial-gradient(ellipse at center,#1a6f9c 0%,var(--stage) 55%,var(--stage-edge) 100%);
    position:relative;
  }
  .screen{position:absolute;top:185px;width:354px;height:630px;overflow:hidden}
  .screen--green{left:198px;background:var(--paper)}
  .screen--sky{left:652px}
  .sky-backdrop{position:absolute;inset:60px 0 0 0;background:linear-gradient(180deg,var(--cloud-top),var(--cloud-bottom))}

  .app-header{position:absolute;left:0;top:0;width:100%;display:flex;align-items:center;color:var(--white)}
  .screen--green .app-header{height:65px;background:var(--green);padding-left:26px}
  .screen--green .app-header::after{content:"";position:absolute;left:240px;top:0;width:1px;height:100%;background:rgba(255,255,255,.35)}
  .screen--sky .app-header{height:60px;background:var(--sky);justify-content:center}
  .brand{display:flex;align-items:center;gap:10px;font-weight:700;font-size:24px;letter-spacing:-.2px}
  .brand-dot{width:14px;height:14px;border-radius:50%;background:var(--white)}

  .progress-badge{position:absolute;width:76px;height:70px;z-index:2}
  .progress-badge svg{position:absolute;inset:0}
  .progress-badge .value{position:absolute;top:10px;width:100%;text-align:center;color:var(--white);font-weight:700;font-size:17px;line-height:1}
  .progress-badge .label{position:absolute;top:29px;width:100%;text-align:center;color:var(--white);font-size:11px}
  .screen--green .progress-badge{left:261px;top:13px}
  .screen--sky .progress-badge{left:142px;top:124px}

  .ribbon{position:absolute;left:0;width:100%;height:70px}
  .ribbon svg{position:absolute;inset:0}
  .ribbon-text{position:absolute;left:0;width:100%;text-align:center;color:var(--white);font-size:17px;display:flex;align-items:center;justify-content:center;gap:6px}
  .ribbon-text b{font-weight:700}
  .screen--green .ribbon{top:100px}
  .screen--sky .ribbon{top:85px}
  .ribbon-text{top:0;height:40px}

  .question{position:absolute;left:21px;font-size:16px;color:var(--ink)}
  .question .step{font-weight:700;margin-right:6px}
  .screen--green .question{top:173px}
  .screen--sky .question{top:210px}
  .screen--sky .question .step{color:var(--sky);font-weight:500}

  .choice{position:absolute;left:15px;width:324px;height:44px;border-radius:4px;display:flex;align-items:center;justify-content:center;font-size:18px;color:var(--white)}
  .screen--sky .choice{left:14px}
  .choice--orange{background:var(--orange)}
  .choice--sky{background:var(--sky)}
  .choice--other{background:var(--white);color:var(--sky);border:1px solid var(--sky)}
  .choice--other svg{position:absolute;right:12px;top:13px}
  .choice--back-green{background:var(--green)}
  .choice--back-sky{background:var(--sky);font-weight:700}
</style>
</head>
<body>

<!-- Screen A: green header variant -->
<section class="screen screen--green">
  <header class="app-header">
    <div class="brand"><span class="brand-dot"></span>TutorPath</div>
  </header>
  <div class="progress-badge">
    <svg viewBox="0 0 76 70" width="76" height="70"><path d="M0 0H76V50L38 70L0 50Z" fill="#1b8fd2"/><path d="M5 0H71V47L38 64L5 47Z" fill="#27a6e6"/></svg>
    <span class="value">0%</span><span class="label">complete</span>
  </div>
  <div class="ribbon">
    <svg viewBox="0 0 354 70" width="354" height="70">
      <path d="M12 12H52V55H12L24 34Z" fill="#1b86c2"/>
      <path d="M342 12H302V55H342L330 34Z" fill="#1b86c2"/>
      <path d="M42 40L52 55V40Z" fill="#0f5f8d"/>
      <path d="M312 40L302 55V40Z" fill="#0f5f8d"/>
      <rect x="42" y="0" width="270" height="40" fill="#27a6dd"/>
    </svg>
    <div class="ribbon-text">Get matched in <b>2 minutes</b>
      <svg width="20" height="20" viewBox="0 0 20 20"><circle cx="10" cy="10" r="8.5" fill="none" stroke="#fff" stroke-width="2"/><path d="M10 5V10H14" fill="none" stroke="#fff" stroke-width="2"/></svg>
    </div>
  </div>
  <p class="question"><span class="step">1/10</span>Please select your field of interest</p>
  <div class="choice choice--orange" style="top:208px">Art &amp; Design</div>
  <div class="choice choice--orange" style="top:261px">Business</div>
  <div class="choice choice--orange" style="top:314px">Criminal Justice</div>
  <div class="choice choice--other" style="top:367px">Other
    <svg width="12" height="18" viewBox="0 0 12 18"><path d="M2 2L10 9L2 16" fill="none" stroke="#13ade0" stroke-width="2.5"/></svg>
  </div>
  <div class="choice choice--back-green" style="top:571px">Back</div>
</section>

<!-- Screen B: sky variant -->
<section class="screen screen--sky">
  <div class="sky-backdrop" role="img" aria-label="Soft sky background with light clouds"></div>
  <header class="app-header">
    <div class="brand"><span class="brand-dot"></span>TutorPath</div>
  </header>
  <div class="ribbon">
    <svg viewBox="0 0 354 70" width="354" height="70">
      <path d="M14 13H56V55H14L28 34Z" fill="#5fb415"/>
      <path d="M340 13H298V55H340L326 34Z" fill="#5fb415"/>
      <path d="M43 40L56 55V40Z" fill="#3c7a08"/>
      <path d="M311 40L298 55V40Z" fill="#3c7a08"/>
      <rect x="43" y="0" width="268" height="40" fill="#6cc117"/>
    </svg>
    <div class="ribbon-text">Get matched in <b>2 minutes</b>
      <svg width="20" height="20" viewBox="0 0 20 20"><circle cx="10" cy="10" r="8.5" fill="none" stroke="#fff" stroke-width="2"/><path d="M10 5V10H14" fill="none" stroke="#fff" stroke-width="2"/></svg>
    </div>
  </div>
  <div class="progress-badge">
    <svg viewBox="0 0 76 70" width="76" height="70"><path d="M0 0H76V50L38 70L0 50Z" fill="#1b8fd2"/><path d="M5 0H71V47L38 64L5 47Z" fill="#27a6e6"/></svg>
    <span class="value">0%</span><span class="label">complete</span>
  </div>
  <p class="question"><span class="step">1/10</span>Please select your field of interest</p>
  <div class="choice choice--sky" style="top:245px">Art &amp; Design</div>
  <div class="choice choice--sky" style="top:297px">Business</div>
  <div class="choice choice--sky" style="top:350px">Business</div>
  <div class="choice choice--other" style="top:404px">Other
    <svg width="12" height="18" viewBox="0 0 12 18"><path d="M2 2L10 9L2 16" fill="none" stroke="#13ade0" stroke-width="2.5"/></svg>
  </div>
  <div class="choice choice--back-sky" style="top:570px">Back</div>
</section>

</body>
</html>
```